Black Matte card with samurai logo which I would like it to be textured and company name on one side and on the other side I would like the company information with the reno (Face logo) Sushi logo. Double Sided card.

majority customers are University students, University sororities and fraternities.

It Company

Reno Sushi
317 W. Harlow Ave
Tucson, AZ 85042
Phone (520)413-6271
Fax (520)357-1846
E-mail: Renosushidesert@mailbox-example.com
FB: Renosushidesert
Twitter: Renosushidesert

• Present Normal

```html
<!DOCTYPE html>
<html lang="en">
<head>
<meta charset="utf-8">
<title>Reno Sushi — Business Card</title>
<link href="https://fonts.googleapis.com/css2?family=Source+Sans+3:wght@400;600&display=swap" rel="stylesheet">
<style>
  :root {
    --bg: #ececea;
    --matte: #232323;
    --matte-light: #2f2f2f;
    --red: #d8232a;
    --deep-red: #a7252a;
    --ink: #111111;
    --text: #474747;
    --white: #ffffff;
    --rule: #c9c9c9;
  }
  html, body {
    margin: 0;
    padding: 0;
    width: 1200px;
    height: 1045px;
    overflow: hidden;
    background: var(--bg);
    font-family: "Source Sans 3", Arial, sans-serif;
  }
  .canvas {
    position: relative;
    width: 1200px;
    height: 1045px;
  }
  .card {
    position: absolute;
    width: 836px;
    height: 477px;
    border-radius: 36px;
    overflow: hidden;
    box-shadow: 0 2px 6px rgba(0,0,0,0.25);
  }
  /* Front side */
  .card-front {
    left: 47px;
    top: 37px;
    background:
      radial-gradient(circle at 50% 45%, var(--matte-light), var(--matte) 75%);
  }
  .front-brand {
    position: absolute;
    inset: 0;
    display: flex;
    align-items: center;
    justify-content: center;
    gap: 22px;
  }
  .brand-dot {
    width: 46px;
    height: 46px;
    border-radius: 50%;
    background: var(--red);
    flex: none;
  }
  .front-name {
    font-size: 86px;
    font-weight: 400;
    color: var(--red);
    letter-spacing: 1px;
    line-height: 1;
  }
  /* Back side */
  .card-back {
    left: 357px;
    top: 548px;
    background: var(--white);
    border: 1px solid #bdbdbd;
  }
  .back-wave {
    position: absolute;
    inset: 0;
  }
  .back-brand {
    position: absolute;
    left: 40px;
    top: 150px;
    width: 320px;
    display: flex;
    align-items: center;
    justify-content: center;
    gap: 14px;
  }
  .back-brand .brand-dot {
    width: 30px;
    height: 30px;
  }
  .back-name {
    font-size: 48px;
    font-weight: 400;
    color: var(--deep-red);
    line-height: 1;
  }
  .divider {
    position: absolute;
    left: 372px;
    top: 112px;
    width: 1px;
    height: 186px;
    background: var(--rule);
  }
  .contact-list {
    position: absolute;
    left: 398px;
    top: 122px;
    margin: 0;
    padding: 0;
    list-style: none;
    color: var(--text);
    font-size: 21.5px;
  }
  .contact-list li {
    display: flex;
    align-items: center;
    gap: 12px;
    height: 32px;
  }
  .contact-list svg {
    width: 20px;
    height: 20px;
    flex: none;
  }
  .address {
    position: absolute;
    left: 398px;
    top: 233px;
    margin: 0;
    font-style: normal;
    color: var(--text);
    font-size: 21.5px;
    line-height: 30px;
  }
  .social-list {
    position: absolute;
    left: 598px;
    top: 400px;
    margin: 0;
    padding: 0;
    list-style: none;
    color: var(--white);
    font-size: 21.5px;
  }
  .social-list li {
    display: flex;
    align-items: center;
    gap: 9px;
    height: 31px;
  }
  .social-square {
    width: 20px;
    height: 20px;
    border-radius: 3px;
    background: #8a8a8a;
    flex: none;
  }
</style>
</head>
<body>
<div class="canvas">

  <section class="card card-front" aria-label="Front of business card">
    <div class="front-brand">
      <span class="brand-dot"></span>
      <span class="front-name">Reno Sushi</span>
    </div>
  </section>

  <section class="card card-back" aria-label="Back of business card">
    <svg class="back-wave" viewBox="0 0 836 477" preserveAspectRatio="none" aria-hidden="true">
      <path d="M0,300 C110,390 260,452 430,452 C600,452 700,360 836,352 L836,477 L0,477 Z" fill="var(--ink)"/>
      <path d="M0,268 C70,330 140,390 215,440 C150,400 70,345 0,300 Z" fill="var(--deep-red)"/>
      <path d="M590,388 C680,345 760,330 836,328 L836,352 C760,352 680,362 590,388 Z" fill="var(--deep-red)"/>
    </svg>

    <div class="back-brand">
      <span class="brand-dot"></span>
      <span class="back-name">Reno Sushi</span>
    </div>

    <div class="divider"></div>

    <ul class="contact-list">
      <li>
        <svg viewBox="0 0 20 20" aria-label="Phone"><circle cx="10" cy="10" r="8.5" fill="none" stroke="var(--deep-red)" stroke-width="1.6"/><path d="M7 5.5 C5.5 8 8 13.5 12.5 14.5 L13.5 12.8 L11.8 11.6 L10.8 12.3 C9.5 11.5 8.6 10.3 8.2 9 L9 8.2 L8.2 6.3 Z" fill="var(--deep-red)"/></svg>
        <span>(520)413-6271</span>
      </li>
      <li>
        <svg viewBox="0 0 20 20" aria-label="Fax"><rect x="5" y="2" width="10" height="16" rx="1.5" fill="var(--deep-red)"/><rect x="6.5" y="4" width="7" height="5" fill="#fff"/><rect x="6.5" y="11" width="2" height="1.5" fill="#fff"/><rect x="9" y="11" width="2" height="1.5" fill="#fff"/><rect x="11.5" y="11" width="2" height="1.5" fill="#fff"/><rect x="6.5" y="14" width="2" height="1.5" fill="#fff"/><rect x="9" y="14" width="2" height="1.5" fill="#fff"/><rect x="11.5" y="14" width="2" height="1.5" fill="#fff"/></svg>
        <span>(520)357-1846</span>
      </li>
      <li>
        <svg viewBox="0 0 20 20" aria-label="Email"><rect x="1.5" y="5" width="17" height="11" rx="1.5" fill="var(--deep-red)"/><path d="M2 6 L10 11.5 L18 6" fill="none" stroke="#fff" stroke-width="1.4"/></svg>
        <span>Renosushidesert@mailbox-example.com</span>
      </li>
    </ul>

    <address class="address">Reno Sushi 317 W. Harlow Ave Tucson<br>AZ 85042</address>

    <ul class="social-list">
      <li><span class="social-square"></span><span>Renosushidesert</span></li>
      <li><span class="social-square"></span><span>Renosushidesert</span></li>
    </ul>
  </section>

</div>
</body>
</html>
```